IT Consultancy Needs Daring Webpage (uncoded)

We are looking for a web page for a small IT firm, Harbor Linkworks. We provide remote IT services, website development and IT consultancy. We are looking for a website that is a bit unique and will look both professional and cutting edge.

We are mainly targeting high cash flow small businesses.
Feel free to play with our yellow/blue theme. We where aiming for similar colours to movie posters i.e the Crimson Ledger, http://qlink.example/x4mTz. Think metallic, flashy and classy like a colourful Zuno.
Updates

We have a website but it is very poor and we would prefer if you did not use it for inspiration.

We quite like this design http://gallery.artfoldex.net/designs/web/?order=24&offset=24#/k7p3wq9

The three cornerstones of our business are Consult, Support and E-Marketing

other designs are welcome as well (different from the the link above)

Target Market(s)

Small Businesses

Industry/Entity Type

Movie

Requirements
Must have
• Space for Home, Services, Contact and Blog menu bars.

Our logo is ok, you are welcome to adjust it a little to meet your needs.

While we appreciate most websites have a dense middle ground for navigation panels, we would like the most important buttons highlighted as well as a slightly interesting background for example, instead of a plain colour background, a slight hint of a pattern or image.
Should not have
• Should not have a banner.

```html
<!DOCTYPE html>
<html lang="en">
<head>
<meta charset="utf-8">
<title>Harbor Linkworks — IT Consultancy</title>
<link rel="stylesheet" href="https://fonts.googleapis.com/css2?family=Carlito:wght@400;700&family=Noto+Sans:wght@400&display=swap">
<style>
  :root {
    --brand-blue: #3a73a0;
    --deep-blue: #14476e;
    --nav-pill: #3d5b78;
    --accent-yellow: #f2b705;
    --ink: #111111;
    --text-grey: #555555;
    --rule-grey: #b9b9b9;
    --page-grey: #e6e6e8;
    --panel-white: #ffffff;
    --white: #ffffff;
  }
  * { margin: 0; padding: 0; box-sizing: border-box; }
  html, body { width: 1200px; height: 1139px; overflow: hidden; }
  body {
    position: relative;
    background: var(--page-grey);
    font-family: "Carlito", "Calibri", sans-serif;
    color: var(--text-grey);
  }
  .abs { position: absolute; }

  /* Navigation */
  .top-nav {
    left: 0; top: 0; width: 1200px; height: 70px;
    background: linear-gradient(#f7f7f7, #ffffff 30%, #dcdcde);
    border-bottom: 1px solid #c9c9cc;
  }
  .nav-link {
    position: absolute; top: 26px; font-size: 17px; color: #444;
  }
  .nav-link--active {
    top: 23px; left: 205px; width: 117px; height: 31px;
    background: var(--nav-pill); color: var(--white); border-radius: 5px;
    text-align: center; line-height: 31px; font-size: 16px;
    box-shadow: 0 1px 2px rgba(0,0,0,.35);
  }

  /* Main panel */
  .main-panel {
    left: 12px; top: 70px; width: 1172px; height: 708px;
    background: linear-gradient(#e9eaee, #ffffff 22%, #ffffff);
  }
  .brand-area {
    left: 12px; top: 70px; width: 397px; height: 327px;
    background: linear-gradient(#eceef1, #ffffff 40%);
    border-bottom: 1px solid var(--rule-grey);
  }
  .brand-mark {
    left: 88px; top: 112px; width: 176px; height: 150px;
    border-radius: 50%; background: var(--deep-blue);
  }
  .brand-name {
    left: 12px; top: 278px; width: 397px; text-align: center;
    font-size: 36px; letter-spacing: 6px; color: var(--ink);
  }

  /* Service overview */
  .sidebar-heading {
    left: 37px; top: 436px; font-size: 23px; color: var(--deep-blue);
    letter-spacing: .3px;
  }
  .sidebar-rule { left: 37px; top: 479px; width: 276px; height: 1px; background: #8a8a8a; }
  .overview-list { left: 55px; top: 505px; width: 330px; list-style: none; }
  .overview-list li {
    position: relative; padding-left: 20px; font-size: 16.5px; line-height: 21px;
    color: var(--text-grey);
  }
  .overview-list li::before {
    content: ""; position: absolute; left: 0; top: 4px;
    border-left: 7px solid var(--accent-yellow);
    border-top: 6px solid transparent; border-bottom: 6px solid transparent;
  }
  .overview-list li + li { margin-top: 19px; }

  /* Feature image */
  .feature-frame {
    left: 410px; top: 106px; width: 748px; height: 371px;
    background: var(--white); border: 1px solid #cfcfcf; border-radius: 4px;
    box-shadow: 0 1px 3px rgba(0,0,0,.2);
  }
  .feature-photo {
    left: 417px; top: 114px; width: 735px; height: 357px;
    background: linear-gradient(100deg, #5d6670 0%, #8e959c 30%, #c9d3dc 55%, #eaf0f5 70%, #2a3038 100%);
  }
  .feature-caption {
    left: 417px; top: 299px; width: 329px; height: 172px;
    background: var(--brand-blue); color: var(--white);
    padding: 19px 0 0 17px; font-size: 26px; line-height: 51px;
  }

  /* Welcome copy */
  .welcome-title {
    left: 425px; top: 516px; font-size: 36px; font-weight: 700; color: var(--deep-blue);
  }
  .welcome-rule { left: 420px; top: 575px; width: 738px; height: 1px; background: var(--rule-grey); }
  .welcome-sub {
    left: 420px; top: 606px; font-size: 24px; font-weight: 700; color: var(--brand-blue);
  }
  .welcome-text {
    left: 420px; top: 672px; width: 740px;
    font-family: "Noto Sans", "Tahoma", sans-serif; font-size: 16.5px;
    line-height: 29px; letter-spacing: .9px; color: #333;
  }

  /* Cornerstones band */
  .cornerstones {
    left: 12px; top: 790px; width: 1172px; height: 301px;
    background: var(--brand-blue); border-radius: 9px;
  }
  .cornerstone-icon { width: 62px; height: 58px; }
  .cornerstone-title {
    font-size: 27px; font-weight: 700; color: var(--white);
  }
  .cornerstone-text {
    font-family: "Noto Sans", "Tahoma", sans-serif; font-size: 13.5px;
    line-height: 22px; color: var(--white);
  }
  .cornerstone-text p + p { margin-top: 22px; }

  /* Footer */
  .site-footer {
    left: 12px; top: 1097px; width: 1172px; height: 38px;
    background: linear-gradient(#ffffff, #e2e2e4);
    text-align: center; font-size: 15px; line-height: 38px; color: #555;
    font-family: "Noto Sans", "Tahoma", sans-serif;
  }
</style>
</head>
<body>
  <nav class="abs top-nav" aria-label="Main navigation">
    <span class="nav-link nav-link--active">About us</span>
    <span class="nav-link" style="left:413px">Services</span>
    <span class="nav-link" style="left:565px">Support</span>
    <span class="nav-link" style="left:718px">Blog</span>
    <span class="nav-link" style="left:885px">Contacts</span>
  </nav>

  <main>
    <div class="abs main-panel"></div>

    <header class="abs brand-area"></header>
    <div class="abs brand-mark" aria-hidden="true"></div>
    <div class="abs brand-name">Harbor Linkworks</div>

    <h2 class="abs sidebar-heading">Service Overview</h2>
    <div class="abs sidebar-rule"></div>
    <ul class="abs overview-list">
      <li>Focus on Latest Trends</li>
      <li>Keeping you ahead in the Fast Moving IT Industry</li>
      <li>Young and Innovative Company</li>
      <li>Keeping you ahead in the Fast Moving IT Industry</li>
    </ul>

    <div class="abs feature-frame"></div>
    <div class="abs feature-photo" role="img" aria-label="Silhouettes of business people walking past large office windows"></div>
    <div class="abs feature-caption">Remote IT services,<br>Website development<br>and IT consultancy</div>

    <h1 class="abs welcome-title">Welcome to Our Websites</h1>
    <div class="abs welcome-rule"></div>
    <h3 class="abs welcome-sub">Big business IT for small businesses</h3>
    <p class="abs welcome-text">We focus on delivering the kind of services big companies&nbsp; have to smaller business around the Illawarra and Sydney.</p>

    <section class="abs cornerstones" aria-label="Our cornerstones"></section>

    <svg class="abs cornerstone-icon" style="left:24px;top:818px" viewBox="0 0 62 58" aria-hidden="true">
      <ellipse cx="31" cy="52" rx="26" ry="5" fill="#f1d48a"/>
      <circle cx="29" cy="26" r="24" fill="#e2a51b"/>
      <rect x="17" y="16" width="24" height="16" rx="4" fill="none" stroke="#fff" stroke-width="2.5"/>
      <path d="M22 32 L20 38 L28 32" fill="#fff"/>
      <line x1="22" y1="22" x2="36" y2="22" stroke="#fff" stroke-width="2"/>
      <line x1="22" y1="27" x2="32" y2="27" stroke="#fff" stroke-width="2"/>
    </svg>
    <div class="abs cornerstone-title" style="left:88px;top:818px">Consult</div>
    <div class="abs cornerstone-text" style="left:79px;top:896px;width:340px">
      <p>Lorem ipsum dolor sit amet conse ctetur adipisicing elit, sed do eiusmod tempor incididunt ut labore et dolore magna aliqua.</p>
      <p>Ut enim ad minim veniam, quis nostrud exercitation ullamco laboris nisi ut aliquip.</p>
    </div>

    <svg class="abs cornerstone-icon" style="left:408px;top:814px" viewBox="0 0 62 58" aria-hidden="true">
      <circle cx="31" cy="18" r="12" fill="#7fd36a"/>
      <path d="M10 56 Q10 32 31 32 Q52 32 52 56 Z" fill="#5cbf47"/>
    </svg>
    <div class="abs cornerstone-title" style="left:477px;top:815px">Support</div>
    <div class="abs cornerstone-text" style="left:477px;top:896px;width:340px">
      <p>Lorem ipsum dolor sit amet conse ctetur adipisicing elit, sed do eiusmod tempor incididunt ut labore et dolore magna aliqua.</p>
      <p>Ut enim ad minim veniam, quis nostrud exercitation ullamco laboris nisi ut aliquip.</p>
    </div>

    <svg class="abs cornerstone-icon" style="left:824px;top:814px" viewBox="0 0 62 58" aria-hidden="true">
      <text x="29" y="44" text-anchor="middle" font-family="Carlito, sans-serif" font-weight="700" font-size="50" fill="#f08a16">@</text>
      <path d="M8 46 Q32 58 52 40 L56 44 L58 32 L46 34 L50 38 Q32 52 8 46 Z" fill="#5cbf47"/>
    </svg>
    <div class="abs cornerstone-title" style="left:900px;top:815px">E-Marketing</div>
    <div class="abs cornerstone-text" style="left:898px;top:896px;width:270px">
      <p>Lorem ipsum dolor sit amet conse ctetur adipisicing elit, sed do eiusmod tempor incididunt ut labore et dolore magna aliqua.</p>
      <p>Ut enim ad minim veniam, quis nostrud exercitation ullamco laboris nisi ut aliquip.</p>
    </div>
  </main>

  <footer class="abs site-footer">Copyright © 2011, HarborLinkworks , All rights reserved.</footer>
</body>
</html>
```